Residential building / Apartments for sale landing page

I need a website / landing page design for my latest development project - a residential building with 70+ apartments for sale. I need the design in layers in Photoshop/Illustrator/InDesign format with all the icons/shapes/maps/graphic assets in vector format (svg, ai, eps) as much as possible.

I prefer white website and please consider the performance/coding experience. We're not making something suitable only for a design contest with fancy parallax effects and confusing animations. We're trying to create usable and clean UI with good UX.

The website will be custom coded, i.e. I'm not using WordPress.

I know that the existing 3D photos are not good but for now you can use them or replace them with some stock photos. I'm going to create new 3D photos soon.

Real Estate Development

1 page

```html
<!DOCTYPE html>
<html lang="en">
<head>
<meta charset="utf-8">
<title>Pine Ridge – Apartments for sale</title>
<link href="https://fonts.googleapis.com/css2?family=Montserrat:wght@400;500;600;700&display=swap" rel="stylesheet">
<style>
:root{
  --blue:#3d63e8;
  --green:#7cc142;
  --green-dark:#5ea22a;
  --ink:#222;
  --text:#555;
  --muted:#888;
  --line:#e3e3e3;
  --soft:#f4f4f4;
  --footer:#2a2a2a;
}
*{box-sizing:border-box;margin:0;padding:0}
html,body{width:1200px;height:4988px;overflow:hidden;background:#fff}
body{font-family:"Montserrat",Arial,sans-serif;color:var(--text);position:relative}
.abs{position:absolute}
.center{left:0;width:1200px;text-align:center}
.section-title{font-size:31px;font-weight:500;color:var(--ink)}
.lead{font-size:12px;line-height:24px;color:var(--text)}

/* top bar */
.topbar{top:0;left:0;width:1200px;height:35px;border-bottom:1px solid var(--line);font-size:10px;color:#444}
.topbar .lang{position:absolute;left:775px;top:12px}
.topbar .lang b{color:#e33;font-weight:500}
.topbar .phone{position:absolute;left:873px;top:11px;font-size:11px}
.topbar .cta{position:absolute;left:990px;top:5px;width:103px;height:22px;background:var(--blue);color:#fff;font-size:10px;text-align:center;line-height:22px}
.brand{top:50px;left:110px;font-size:21px;font-weight:700;color:var(--ink);display:flex;align-items:center;gap:8px}
.brand i{display:block;width:14px;height:14px;background:var(--green)}
.nav{top:55px;left:668px;display:flex;gap:26px;font-size:12px;font-weight:500;color:var(--ink)}
.nav .on{color:var(--green)}

.hero{top:93px;left:0;width:1200px;height:464px;background:linear-gradient(180deg,#b9c7cf 0%,#8d9a82 38%,#d9dcd6 62%,#7d9a5a 100%)}
.hero-rule{top:553px;left:0;width:1200px;height:5px;background:var(--green)}

.sale h1{position:absolute;left:110px;top:598px;font-size:38px;font-weight:700;color:var(--ink)}
.sale .sub{position:absolute;left:110px;top:648px;font-size:21px;color:#555}
.sale .price{position:absolute;left:110px;top:682px;font-size:14px;color:var(--green);font-weight:500}
.buy{top:606px;left:913px;width:174px;height:44px;background:var(--blue);color:#fff;font-size:17px;display:flex;align-items:center;justify-content:center;gap:8px}
.ring{display:inline-block;width:13px;height:13px;border:1.5px solid currentColor;border-radius:50%}

.welcome h2{position:absolute;left:110px;top:848px;font-size:32px;font-weight:400;color:var(--ink)}
.welcome h2 span{color:var(--green)}
.welcome p{position:absolute;left:110px;top:907px;width:470px;font-size:11px;line-height:22.5px}
.blob{border-radius:48% 52% 58% 42%/44% 46% 54% 56%;border-bottom:5px solid var(--green);border-left:2px solid var(--green)}
.blob-welcome{top:784px;left:633px;width:454px;height:406px;background:linear-gradient(160deg,#e9ecef,#b7bfc6 55%,#7b7b6e)}

.benefit-lead{top:1318px;left:110px;width:484px;height:153px;background:var(--blue);color:#fff;font-size:13px;line-height:23px;padding:30px 26px}
.benefit{width:200px;text-align:center;font-size:14px;color:#333}
.benefit svg{display:block;margin:0 auto 12px;width:70px;height:64px;fill:none;stroke:var(--green);stroke-width:2.4;stroke-linecap:round;stroke-linejoin:round}

.floors{top:1970px;left:110px;width:983px;height:41px;display:flex}
.floors div{flex:1;background:var(--green);color:#fff;font-size:11px;text-align:center;line-height:41px;border-right:2px solid #fff}
.floors .on{background:var(--blue);position:relative}
.floors .on:after{content:"";position:absolute;left:50%;bottom:-9px;margin-left:-9px;border:9px solid transparent;border-bottom:0;border-top-color:var(--blue)}
.types{top:2078px;left:364px;display:flex;gap:5px}
.types div{height:25px;padding:0 9px;background:#e9e9e9;font-size:11px;line-height:25px;color:#444}
.types .on{background:#222;color:#fff}
.plan{top:2123px;left:130px;width:389px;height:315px;background:linear-gradient(135deg,#e6e6e6,#bdbdbd)}
.spec{top:2154px;left:561px;width:532px;border-collapse:collapse;font-size:11px}
.spec td{height:46px;border:1px solid #eee;padding:0 12px;color:#333}
.spec td:nth-child(odd){font-weight:600;background:#fafafa}
.spec td:nth-child(even){text-align:center}
.price{top:2410px;left:561px;font-size:19px;color:#222}
.price b{color:var(--green);font-weight:500;margin-right:12px}

.blob-feature{top:2695px;left:116px;width:455px;height:405px;background:linear-gradient(160deg,#f2f2ef,#c8d2da 45%,#8aa0b4);border-radius:52% 48% 40% 60%/46% 52% 48% 54%}
.features{top:2733px;left:633px;width:455px;list-style:none;font-size:11px;line-height:19px}
.features li{margin-bottom:11px}
.features b{color:var(--green);font-weight:700}

.loc-tabs{top:3315px;left:344px;display:flex;gap:4px}
.loc-tabs div{width:98px;height:27px;background:var(--green);color:#fff;font-size:11px;text-align:center;line-height:27px}
.loc-tabs .on{background:var(--blue)}
.map{top:3367px;left:0;width:1200px;height:455px;background:linear-gradient(135deg,#eef0f2,#e2e6ea 50%,#eceeea)}
.map-card{top:3578px;left:588px;width:140px;height:44px;background:#fff;box-shadow:0 1px 4px rgba(0,0,0,.2);font-size:10px;text-align:center;padding-top:8px;color:#333}

.gal-lead{top:3969px;left:110px;width:236px;height:255px;background:var(--blue);color:#fff;font-size:12px;line-height:23px;padding:28px 24px}
.shot{top:3969px;width:236px;height:211px}
.gal-date{top:4204px;font-size:12px;color:#444}
.view{top:4195px;width:89px;height:31px;background:var(--green);color:#fff;font-size:12px;display:flex;align-items:center;justify-content:center;gap:6px}

.grass{top:4276px;left:0;width:1200px;height:410px;background:linear-gradient(180deg,#fff 0%,#e8efe0 45%,#8fa873 100%)}
.dark{top:4683px;left:0;width:1200px;height:305px;background:var(--footer)}
.card-left{top:4385px;left:155px;width:507px;height:485px;background:#fff}
.card-right{top:4385px;left:662px;width:381px;height:485px;background:var(--blue);color:#fff}
.contact h2{position:absolute;left:37px;top:44px;font-size:29px;font-weight:500;color:var(--ink)}
.field{position:absolute;border:1px solid #bbb;font-size:11px;color:#555;padding:14px 12px}
.agree{position:absolute;left:37px;top:334px;font-size:10px;display:flex;align-items:center;gap:8px}
.agree i{width:12px;height:12px;border:1px solid #aaa}
.submit{position:absolute;left:37px;top:368px;width:154px;height:40px;background:var(--green);color:#fff;font-size:13px;text-align:center;line-height:40px}
.req{position:absolute;left:37px;top:423px;font-size:9px;color:#e33}
.card-right .name{position:absolute;left:0;width:381px;top:128px;text-align:center;font-size:34px;font-weight:700}
.info{position:absolute;left:38px;display:flex;align-items:center;gap:18px;font-size:11px;line-height:17px}
.info .dot{flex:none;width:42px;height:42px;border:1.5px solid rgba(255,255,255,.6);border-radius:50%;display:flex;align-items:center;justify-content:center}
.info svg{width:16px;height:16px;fill:none;stroke:#fff;stroke-width:2}
.footnav{top:4896px;left:158px;display:flex;gap:18px;font-size:10px;color:#fff}
.social{top:4893px;left:1000px;display:flex;gap:8px}
.social i{width:16px;height:16px;border:1.5px solid #fff;border-radius:50%}
.copy{top:4952px;font-size:10px;color:#ccc}
</style>
</head>
<body>

<header>
  <div class="abs topbar">
    <span class="lang">Language: BG <b>EN</b></span>
    <span class="phone">+359 10 2000 4455</span>
    <span class="cta">Contact us</span>
  </div>
  <div class="abs brand"><i></i>PINE RIDGE</div>
  <nav class="abs nav"><span class="on">Pine Ridge</span><span>The project</span><span>Apartments/Sales</span><span>Location</span><span>Gallery</span></nav>
</header>

<div class="abs hero" role="img" aria-label="Render of the terraced white residential building covered in greenery, mountain behind"></div>
<div class="abs hero-rule"></div>

<section class="sale">
  <h1>Sale of Apartments</h1>
  <div class="sub">Directly from the investor with 10% discount</div>
  <div class="price">Price from 200 EUR/m2</div>
  <div class="abs buy">Buy now <span class="ring"></span></div>
</section>
<svg class="abs" style="top:700px;left:0" width="1200" height="60" viewBox="0 0 1200 60"><path d="M0 42 C 300 40 700 44 980 26 C 1080 18 1150 10 1200 4 L1200 26 C 1140 22 1080 30 980 38 C 700 52 300 48 0 44Z" fill="var(--green)"/></svg>

<section class="welcome">
  <h2>Welcome to <span>Pine Ridge</span></h2>
  <p>Lorem ipsum dolor sit amet, consectetur adipiscing elit. Sed bibendum elit orci, vitae ultricies neque finibus quis. Maecenas a felis eu ipsum molestie volutpat ut nec nisl. Curabitur ut leo ac elit ultrices iaculis eget eget justo. Sed placerat nulla ac egestas finibus. Etiam hendrerit quis tellus nec maximus. Duis eget lacus ut nulla fermentum vehicula eu a tortor. Nam viverra pretium augue, vel dapibus magna porttitor eget. Sed luctus orci eget finibus pharetra. In vitae nisl justo.</p>
  <div class="abs blob blob-welcome" role="img" aria-label="Photo of a couple on a terrace looking out over the city"></div>
</section>

<section class="benefits">
  <h2 class="abs center section-title" style="top:1232px">Benefits</h2>
  <div class="abs benefit-lead">Lorem ipsum dolor sit amet, consectetur adipiscing elit. Sed bibendum elit orci, vitae ultricies neque finibus quis. Lorem ipsum dolor sit amet, consectetur adipiscing elit.</div>

  <div class="abs benefit" style="left:624px;top:1352px"><svg viewBox="0 0 70 64"><circle cx="26" cy="26" r="12"/><circle cx="44" cy="24" r="13"/><path d="M26 38v16M44 37v17M12 54h46"/></svg>Green areas and gardens</div>
  <div class="abs benefit" style="left:877px;top:1344px"><svg viewBox="0 0 70 64"><rect x="14" y="4" width="42" height="56"/><path d="M35 4v56M14 32h42"/><path d="M42 12h6a4 4 0 0 1 0 8h-6v-8M42 40h6a4 4 0 0 1 0 8h-6v-8"/></svg>Parking spaces</div>

  <div class="abs benefit" style="left:128px;top:1518px"><svg viewBox="0 0 70 64"><circle cx="18" cy="44" r="11"/><circle cx="52" cy="44" r="11"/><path d="M18 44l10-18h18l6 18M28 26l8 18h-18M36 44l10-18M24 18h8"/></svg>Bicycle parking</div>
  <div class="abs benefit" style="left:377px;top:1518px"><svg viewBox="0 0 70 64"><path d="M12 32h46M16 22v20M10 26v12M54 22v20M60 26v12"/></svg>Outside workout area</div>
  <div class="abs benefit" style="left:629px;top:1518px"><svg viewBox="0 0 70 64"><path d="M22 8h26v52H22zM22 8l18 6v46"/><circle cx="35" cy="36" r="2"/></svg>NFC controlled access</div>
  <div class="abs benefit" style="left:877px;top:1518px"><svg viewBox="0 0 70 64"><path d="M35 50c-8-6-12-16-8-28 4 12 8 14 8 28zM35 50c8-6 12-16 8-28-4 12-8 14-8 28zM35 50c-12 0-20-8-22-16 10 2 18 6 22 16zM35 50c12 0 20-8 22-16-10 2-18 6-22 16z"/></svg>Outdoor Yoga area</div>

  <div class="abs benefit" style="left:128px;top:1686px"><svg viewBox="0 0 70 64"><path d="M10 26C14 10 56 10 60 26zM35 16v38M20 54h30M14 40h12v14M56 40H44v14"/></svg>Relaxation area</div>
  <div class="abs benefit" style="left:377px;top:1684px"><svg viewBox="0 0 70 64"><circle cx="48" cy="22" r="12"/><path d="M48 34v20M8 54h56M12 54V40h16l10 14M12 40l8-10h8"/></svg>Childrens play ground</div>
  <div class="abs benefit" style="left:624px;top:1686px"><svg viewBox="0 0 70 64"><path d="M26 8v34M44 8v34M26 18h18M26 30h18M10 46c6-4 10 4 16 0s10 4 16 0 10 4 16 0M10 56c6-4 10 4 16 0s10 4 16 0 10 4 16 0"/></svg>Pool</div>
  <div class="abs benefit" style="left:877px;top:1686px"><svg viewBox="0 0 70 64"><path d="M16 8l38 48M54 8L16 56M46 8l10 12"/></svg>Restaurant</div>
</section>

<section class="apartments">
  <h2 class="abs center section-title" style="top:1864px">Apartments</h2>
  <p class="abs center lead" style="top:1914px">Lorem ipsum dolor sit amet, consectetur adipiscing elit. Sed bibendum elit orci, vitae ultricies neque finibus quis. Lorem ipsum dolor sit amet.</p>
  <div class="abs floors"><div class="on">Floor 1</div><div>Floor 2</div><div>Floor 3</div><div>Floor 4</div><div>Floor 5</div><div>Floor 6</div><div>Floor 7</div><div style="border:0">Floor 8</div></div>
  <div class="abs center" style="top:2035px;font-size:14px;color:#333">Apartment Type</div>
  <div class="abs types"><div class="on">A 11</div><div>A 12</div><div>A 13</div><div>A 14</div><div>B 11</div><div>B 12</div><div>B 13</div><div>C 11</div><div>C 12</div><div>C 13</div><div>C 14</div></div>
  <div class="abs plan" role="img" aria-label="Floor plan drawing of apartment A 11"></div>
  <table class="abs spec">
    <tr><td>Unit</td><td>1</td><td>Status</td><td>Available</td></tr>
    <tr><td>Entrance</td><td>2</td><td>View</td><td>Yes</td></tr>
    <tr><td>Beds</td><td>2</td><td>Parking space</td><td>Yes</td></tr>
    <tr><td>Bathrooms</td><td>2</td><td>MM tax</td><td>12%</td></tr>
    <tr><td>Area</td><td>148.6449 m²</td><td>Unit plan + Floor plan</td><td>View</td></tr>
  </table>
  <div class="abs price"><b>Price:</b>389 EUR/m2</div>
</section>

<section class="construction">
  <h2 class="abs center section-title" style="top:2521px">Construction features</h2>
  <p class="abs center lead" style="top:2586px">Lorem ipsum dolor sit amet, consectetur adipiscing elit. Sed bibendum elit orci, vitae ultricies neque finibus quis. Lorem ipsum dolor sit amet,<br>consectetur adipiscing elit. Sed bibendum elit orci, vitae ultricies neque finibus quis.</p>
  <div class="abs blob blob-feature" role="img" aria-label="Interior of a bright living room with a large window over the city"></div>
  <ul class="abs features">
    <li><b>Norvel Windows</b> - 5 chamber noise reducing glazing with high temperature and noise insulation efficiency</li>
    <li><b>Calder brick</b> - Austrian Calder ThermoCore bricks with porous system and 25 cm thick outer walls</li>
    <li><b>High Ceilings</b> - 2.70m high ceilings giving the light and space you need</li>
    <li><b>Thermal Insulation System Stavio</b> - Stavio Silicone Plaster Thermal Insulation System 10 cm thick and 15 cm thick from the north walls</li>
    <li><b>Air conditioners</b> - All air conditioners piping systems are installed - ready to plug in the inside and outside body of the aircon system</li>
    <li><b>HPL ventilated facade Panelor GmbH</b> - Suspended ventilated facade with highly pressed laminated panels by Panelor GmbH in wood color</li>
    <li><b>Panoramic Overall view over looking the park</b> - Giving you the everyday glimpse over the inside garden and putting a smile on your face</li>
    <li><b>Water proofing with PVC membrane Hydra</b> - PVC membrane with high puncture and tear resistance, UV resistance and vapor permeability</li>
  </ul>
</section>

<section class="location">
  <h2 class="abs center section-title" style="top:3211px">Location</h2>
  <p class="abs center lead" style="top:3261px">Lorem ipsum dolor sit amet, consectetur adipiscing elit. Sed bibendum elit orci, vitae ultricies neque finibus quis. Lorem ipsum dolor sit amet.</p>
  <div class="abs loc-tabs"><div class="on">Pine Ridge</div><div>Metro</div><div>Bus stops</div><div>School</div><div>Market</div></div>
  <div class="abs map" role="img" aria-label="Street map of the surrounding neighbourhood with the building marked"></div>
  <div class="abs map-card">Pine Ridge<br>Apartments</div>
  <svg class="abs" style="top:3573px;left:718px" width="20" height="26" viewBox="0 0 20 26"><path d="M10 25C4 16 2 13 2 9a8 8 0 0 1 16 0c0 4-2 7-8 16z" fill="#e33"/><circle cx="10" cy="9" r="3" fill="#fff"/></svg>
</section>

<section class="gallery">
  <h2 class="abs center section-title" style="top:3885px">Gallery</h2>
  <div class="abs gal-lead">Lorem ipsum dolor sit amet, consectetur adipiscing elit. Sed bibendum elit orci, vitae ultricies neque finibus quis. Lorem ipsum dolor sit amet, consectetur adipiscing elit. Sed bibendum elit orci, vitae ultricies neque finibus quis.</div>
  <div class="abs shot" style="left:360px;background:linear-gradient(160deg,#c9c3b8,#8a7f72 60%,#5d554c)" role="img" aria-label="Construction site photo, building frame in progress, April 2021"></div>
  <div class="abs shot" style="left:608px;background:linear-gradient(160deg,#b8c8d4,#6f8797 60%,#4c5a63)" role="img" aria-label="Construction site photo, foundation slab and rebar, March 2021"></div>
  <div class="abs shot" style="left:857px;background:linear-gradient(160deg,#d8c4a4,#b39670 60%,#8a7050)" role="img" aria-label="Construction site photo, excavation with trucks, February 2021"></div>
  <div class="abs gal-date" style="left:364px">April 2021</div><div class="abs view" style="left:504px">View <span class="ring"></span></div>
  <div class="abs gal-date" style="left:612px">March 2021</div><div class="abs view" style="left:752px">View <span class="ring"></span></div>
  <div class="abs gal-date" style="left:861px">February 2021</div><div class="abs view" style="left:1004px">View <span class="ring"></span></div>
</section>

<section class="contact">
  <div class="abs grass" role="img" aria-label="Soft blurred grass field backdrop"></div>
  <div class="abs dark"></div>
  <div class="abs card-left">
    <h2>Contact us</h2>
    <div class="field" style="left:37px;top:114px;width:445px;height:42px">Name *</div>
    <div class="field" style="left:37px;top:174px;width:220px;height:42px">Email *</div>
    <div class="field" style="left:271px;top:174px;width:211px;height:42px">Phone *</div>
    <div class="field" style="left:37px;top:240px;width:445px;height:77px">Message</div>
    <div class="agree"><i></i>I agree with the privacy policy of Pine Ridge</div>
    <div class="submit">SUBMIT</div>
    <div class="req">* Fields are important</div>
  </div>
  <div class="abs card-right">
    <div class="name">PINE RIDGE</div>
    <div class="info" style="top:234px"><span class="dot"><svg viewBox="0 0 16 16"><path d="M8 15C4 10 3 8 3 6a5 5 0 0 1 10 0c0 2-1 4-5 9z"/><circle cx="8" cy="6" r="1.5"/></svg></span>Lorem ipsum dolor sit amet, consectetur<br>adipiscing elit</div>
    <div class="info" style="top:309px;font-size:19px;font-weight:600"><span class="dot"><svg viewBox="0 0 16 16"><path d="M4 2l3 3-2 2c1 2 2 3 4 4l2-2 3 3-2 2C7 14 2 9 2 4z"/></svg></span>+ 77 10 2000 4455</div>
    <div class="info" style="top:379px"><span class="dot"><svg viewBox="0 0 16 16"><rect x="2" y="4" width="12" height="9"/><path d="M2 4l6 5 6-5"/></svg></span>info@pineridge-homes.com</div>
  </div>
  <nav class="abs footnav"><span>Pine Ridge</span><span>The project</span><span>Apartments/Sales</span><span>Location</span><span>Gallery</span></nav>
  <div class="abs social"><i></i><i></i></div>
  <div class="abs center copy">Copyright © 2021 pineridge-homes.com All Right Reserved</div>
</section>

</body>
</html>
```